New Business Card Design for Manufacturing

We are an engineering/manufacturing company that offers Advanced machining/assembly/engineering services, as well as innovative products for the heavy duty engine cooling markets.

We are looking to get a new business card designed that is clean and modern looking, but still fits the wide range of technical/skilled work we do.

- We hope to use this design as the base for other design work in new Presentations, web, and print work.

Industry/Entity Type

Engineering

Contact Information for Business Card

Our preferred color of blue is (RGB) 22/71/159 but can vary slightly from that color. Our content will be our Logo and full company name (Vantrell Forge Works, Inc.), company address, name, job title, phone number with extension, cell number, fax number, website, and email address on the cards.
We'd like the full company name next to the logo, but we are open to other interpretations of that layout.
Preferably, we would like the back side to be clean with just our logo, and the front to contain all of the contact information.

Colors
2f74b4
0355a3
85abd2

Requirements
Must have
• - Logo, company name, needed content - We are open to interpretation beyond that.
• - Standard size business card.
• - Horizontal orientation.
• - Enough space for lengthy names / job titles (for example, a job title could read "Directory of Human Resources" or "V.P. of Governmental Affairs"). We need this to look clean, whether the title be short (CEO) or long (as described above).

```html
<!DOCTYPE html>
<html lang="en">
<head>
<meta charset="utf-8">
<title>Vantrell Forge Works, Inc. — Business Card</title>
<link href="https://fonts.googleapis.com/css2?family=Lato:wght@400;700&display=swap" rel="stylesheet">
<style>
  :root {
    --brand-blue: #0f4fa0;
    --brand-blue-deep: #0355a3;
    --accent-grey: #8a8f96;
    --ink: #2a2d33;
    --paper: #ffffff;
    --backdrop: #1b1b1d;
  }
  * { box-sizing: border-box; margin: 0; padding: 0; }
  html, body {
    width: 1200px; height: 963px; overflow: hidden;
    background: var(--backdrop);
    font-family: "Lato", sans-serif;
  }
  .stage {
    width: 1200px; height: 963px;
    display: flex; flex-direction: column; align-items: center; justify-content: center;
    gap: 60px;
  }
  .card {
    position: relative;
    width: 620px; height: 354px;
    border-radius: 16px;
    overflow: hidden;
  }
  /* Front */
  .card-front { background: var(--paper); }
  .card-front .wave { position: absolute; inset: 0; width: 100%; height: 100%; }
  .brand {
    position: absolute; left: 34px; top: 44px;
    display: flex; align-items: center; gap: 10px;
  }
  .brand-mark { width: 16px; height: 16px; background: var(--brand-blue); }
  .brand-name {
    color: var(--brand-blue); font-weight: 700; font-size: 20px;
    letter-spacing: 0.5px; text-transform: uppercase;
  }
  .divider {
    position: absolute; left: 306px; top: 92px;
    width: 1.5px; height: 190px; background: var(--brand-blue);
  }
  .contact {
    position: absolute; left: 330px; top: 92px; width: 270px;
    color: var(--ink);
  }
  .person-name {
    color: var(--brand-blue); font-size: 22px; font-weight: 400;
    letter-spacing: 2px; text-transform: uppercase; line-height: 1.1;
  }
  .person-title { font-size: 13px; margin-top: 3px; }
  .address { font-size: 13px; line-height: 1.35; margin-top: 12px; }
  .lines { list-style: none; margin-top: 12px; font-size: 13px; line-height: 1.45; }
  .lines li { display: flex; align-items: center; gap: 8px; }
  .lines svg { width: 10px; height: 10px; flex: none; }
  .icon { fill: var(--brand-blue); }
  /* Back */
  .card-back {
    background: var(--brand-blue);
    display: flex; flex-direction: column; align-items: center; justify-content: center;
    gap: 38px; color: var(--paper);
  }
  .card-back .brand { position: static; }
  .card-back .brand-mark { background: var(--paper); width: 22px; height: 22px; }
  .card-back .brand-name { color: var(--paper); font-size: 30px; }
  .website { font-size: 15px; letter-spacing: 1.5px; }
</style>
</head>
<body>
<main class="stage">
  <section class="card card-front" aria-label="Business card front">
    <svg class="wave" viewBox="0 0 620 354" preserveAspectRatio="none" aria-hidden="true">
      <path d="M0,232 C150,238 250,290 320,322 C390,352 500,350 620,346" fill="none" stroke="var(--accent-grey)" stroke-width="4"/>
      <path d="M0,242 C150,250 245,300 315,332 C380,360 500,356 620,354 L0,354 Z" fill="var(--brand-blue)"/>
    </svg>
    <div class="brand">
      <span class="brand-mark"></span>
      <span class="brand-name">Vantrell Forge Works, Inc.</span>
    </div>
    <div class="divider"></div>
    <div class="contact">
      <p class="person-name">Dorian Kessler</p>
      <p class="person-title">Directory of Human Resources</p>
      <p class="address">4870 Harlow Ridge Rd.<br>Calder Falls, OH 44912</p>
      <ul class="lines">
        <li><svg viewBox="0 0 10 10"><path class="icon" d="M2,0 L4,2 L3,4 C4,6 5,7 6,7 L8,6 L10,8 L8,10 C4,10 0,6 0,2 Z"/></svg>1234- ext</li>
        <li><svg viewBox="0 0 10 10"><rect class="icon" x="2.5" y="0" width="5" height="10" rx="1"/></svg>555-014-2276</li>
        <li><svg viewBox="0 0 10 10"><rect class="icon" x="0" y="3" width="10" height="6" rx="1"/><rect class="icon" x="2" y="0" width="6" height="3"/></svg>(555)014-2290</li>
        <li><svg viewBox="0 0 10 10"><rect x="0.5" y="2" width="9" height="6" fill="none" stroke="var(--brand-blue)"/><path d="M0.5,2 L5,6 L9.5,2" fill="none" stroke="var(--brand-blue)"/></svg>dkessler@vantrellforge.com</li>
        <li><svg viewBox="0 0 10 10"><circle class="icon" cx="5" cy="5" r="5"/></svg>www.vantrellforge.com</li>
      </ul>
    </div>
  </section>

  <section class="card card-back" aria-label="Business card back">
    <div class="brand">
      <span class="brand-mark"></span>
      <span class="brand-name">Vantrell Forge Works, Inc.</span>
    </div>
    <p class="website">www.yourwebsite.com</p>
  </section>
</main>
</body>
</html>
```